Corvane Lending Partners. Professional and Established Company

A full service finance company specializing in obtaining capital for small business. Business Lending advisor, helping small business owners access the capital they need to launch, grow, or sustain their business. Many of our programs offer flexible guidelines to overcome common obstacles such as credit score, credit history, and time in business, financials, and industry type. Our streamlined funding process makes getting a business loan, business line of credit, stated income commercial real estate loan, a smooth and stress free experience.SOME OF THE MOST COMMON NEEDS FOR BUSINESS CAPITAL:• Working Capital• Debt Consolidations (loans, merchant cash advances, etc.)• Payroll• Operating Expenses• Inventory• Equipment Financing• Commercial Real Estate (Purchase, Fix & Flip, Rehab, Renovations)• Business Acquisitions• Business ExpansionWe like the websites:www.quillmorecf.com they are in the same industry and provide the same servicesWe are wanting to be able to update when we do press releases and such using Word Press. Our look should be very professional and we will be adding Our Team Professional Bios and Headshots.

Industry/Entity Type

Finance

Number of Pages Required

5+ page

Font styles to use
Serif
Sans Serif

Requirements
Must have
• We want to copy quillmorecf.com
• We need:
• Home Page
• About Us
• Loan Programs
• Loan Criteria
• News
• Apply Now
• Contact
Nice to have
• See quillmorecf.com
Should not have
• Need professional design. Nothing bright or abstract

```html
<!DOCTYPE html>
<html lang="en">
<head>
<meta charset="utf-8">
<title>Corvane Lending Partners</title>
<link href="https://fonts.googleapis.com/css2?family=Cinzel:wght@400;700&family=Lato:wght@400;700&display=swap" rel="stylesheet">
<style>
:root{
  --blue:#2f7de1;
  --blue-dark:#1f62bd;
  --ink:#1d1d1d;
  --text:#3a3a3a;
  --muted:#666;
  --grey-bg:#e9ecee;
  --white:#fff;
  --line:#d8dde2;
}
*{box-sizing:border-box;margin:0;padding:0}
html,body{width:1200px;height:3516px;overflow:hidden}
body{font-family:'Lato',sans-serif;color:var(--text);background:var(--white);position:relative}
.serif{font-family:'Cinzel',serif}
section,header,footer,nav{position:absolute;left:0;width:1200px}
.center{text-align:center}
.eyebrow{font-family:'Cinzel',serif;font-size:17px;letter-spacing:2px;color:var(--ink);text-align:center}
.section-title{font-family:'Cinzel',serif;font-size:38px;letter-spacing:2px;color:var(--ink);text-align:center;font-weight:400}
.rule{width:150px;height:1px;background:#bfc6cc;margin:0 auto;position:relative}
.rule::after{content:"";position:absolute;left:55px;top:-1px;width:40px;height:3px;background:var(--blue)}
.btn{display:inline-block;background:var(--blue);color:#fff;font-weight:700;font-size:14px;letter-spacing:.5px;border-radius:22px;width:145px;height:40px;line-height:40px;text-align:center}
.arrow-btn{position:absolute;width:36px;height:36px;border-radius:50%;background:#fff;border:1px solid #cfd5da;display:flex;align-items:center;justify-content:center}

/* header */
.topbar{top:0;height:78px;background:#fff}
.brand{position:absolute;left:143px;top:14px;font-family:'Lato',sans-serif;font-weight:700;font-size:26px;color:var(--blue);letter-spacing:.5px}
.contact-line{position:absolute;left:870px;display:flex;align-items:center;gap:12px;font-size:13px;color:#555}
.contact-line .dot{width:22px;height:22px;border-radius:50%;background:var(--blue);display:flex;align-items:center;justify-content:center}
.mainnav{top:78px;height:56px;background:var(--blue)}
.mainnav ul{list-style:none;position:absolute;left:143px;top:0;display:flex;height:56px}
.mainnav li{color:#fff;font-size:13px;padding:0 11px;line-height:56px;letter-spacing:.3px}
.mainnav li.active{background:#e3e7ea;color:var(--blue)}
.social{position:absolute;left:970px;top:15px;display:flex;gap:10px}
.social span{width:26px;height:26px;border-radius:50%;border:1.5px solid #fff}

/* hero */
.hero{top:134px;height:508px;background:linear-gradient(100deg,#f2f6fa 0%,#cfe3f2 35%,#a9d0ea 60%,#5ea8d8 80%,#d5e8f4 100%)}
.hero-copy{position:absolute;left:0;width:1200px;top:142px;text-align:center}
.hero-copy .kicker{font-weight:700;font-size:19px;color:var(--ink);letter-spacing:.3px}
.hero-copy h1{font-family:'Cinzel',serif;font-weight:400;font-size:64px;line-height:70px;color:var(--ink);margin-top:10px;letter-spacing:1px}
.hero-copy p{font-size:14px;font-weight:700;color:#222;width:560px;margin:16px auto 0;line-height:20px}
.hero-copy .btn{margin-top:42px}

/* closed loans */
.closed{top:642px;height:427px;background:var(--grey-bg)}
.closed .eyebrow{margin-top:76px}
.closed .section-title{margin-top:8px}
.closed .rule{margin-top:14px}
.loan-cards{position:absolute;left:237px;top:192px;width:729px;height:161px;display:flex;background:#fff;box-shadow:0 2px 8px rgba(0,0,0,.12)}
.loan-card{flex:1;text-align:center;padding-top:36px}
.loan-card.featured{background:var(--blue);color:#fff}
.loan-card .kind{font-weight:700;font-size:13px;color:var(--ink)}
.loan-card .amount{font-weight:700;font-size:26px;color:var(--ink);margin-top:8px}
.loan-card .note{font-size:13px;color:#333;margin-top:12px;line-height:17px}
.loan-card.featured .kind,.loan-card.featured .amount,.loan-card.featured .note{color:#fff}

/* about */
.about{top:1069px;height:370px;background:#fff}
.about .eyebrow{margin-top:75px}
.about .section-title{margin-top:8px}
.about .rule{margin-top:16px}
.about p{width:900px;margin:26px auto 0;font-size:12.5px;line-height:21px;text-align:center;color:#333}
.about p b{color:var(--blue);font-weight:700}
.about .btn{margin-top:30px}

/* programs */
.programs{top:1439px;height:863px;background:var(--grey-bg)}
.programs .eyebrow{margin-top:68px}
.programs .section-title{margin-top:10px}
.programs .rule{margin-top:16px}
.programs .intro{width:900px;margin:30px auto 0;font-size:12.5px;line-height:21px;text-align:center;color:#333}
.program-grid{position:absolute;left:141px;top:290px;width:920px;display:grid;grid-template-columns:repeat(3,300px);grid-auto-rows:158px;gap:12px 10px}
.program{background:#fff;text-align:center;padding-top:16px}
.program .icon{width:42px;height:42px;margin:0 auto}
.program h3{font-size:13.5px;font-weight:700;color:var(--ink);margin-top:12px;letter-spacing:.2px}
.program p{font-size:12px;line-height:18px;width:200px;margin:4px auto 0;color:#333}
.program.featured{background:var(--blue)}
.program.featured h3,.program.featured p{color:#fff}

/* team */
.team{top:2302px;height:600px;background:#fff}
.team .eyebrow{margin-top:70px}
.team .section-title{margin-top:6px}
.team .rule{margin-top:16px}
.member{position:absolute;top:183px;width:261px}
.member .photo{height:217px}
.member .info{background:#dde2e5;text-align:center;height:63px;padding-top:14px;position:relative}
.member .info .name{font-weight:700;font-size:15px;color:var(--ink)}
.member .info .role{font-size:11px;color:#666;margin-top:4px}
.member .chev{position:absolute;left:110px;top:-20px;width:40px;height:40px;border-radius:50%;background:#dde2e5;display:flex;align-items:center;justify-content:center}
.member.open .info{background:var(--blue);height:113px;margin-top:-37px;padding-top:32px}
.member.open .info .name,.member.open .info .role{color:#fff}
.member.open .chev{background:var(--blue)}
.member .detail{color:#fff;font-size:14px;margin-top:10px;display:flex;align-items:center;justify-content:center;gap:8px}
.member .detail.small{font-size:11px;margin-top:6px}

/* news */
.news{top:2902px;height:532px;background:var(--grey-bg)}
.news .eyebrow{margin-top:72px}
.news .section-title{margin-top:2px}
.news .rule{margin-top:16px}
.post{position:absolute;top:183px;width:260px}
.post .frame{background:#fff;padding:8px;box-shadow:0 1px 4px rgba(0,0,0,.12)}
.post .photo{height:200px}
.post .date{position:absolute;left:-10px;top:-20px;width:52px;height:56px;background:var(--blue);color:#fff;text-align:center;font-weight:700;font-size:16px;line-height:18px;padding-top:8px}
.post h4{font-size:15px;font-weight:700;color:var(--ink);line-height:19px;margin-top:16px;width:230px}
.post .more{font-size:13px;color:var(--blue);margin-top:12px;display:flex;align-items:center;gap:8px}

/* footer */
.footer{top:3434px;height:82px;background:var(--blue);color:#fff}
.foot-item{position:absolute;top:22px;display:flex;gap:12px;font-size:12px;line-height:17px}
.foot-item .dot{width:22px;height:22px;border-radius:50%;background:#fff;display:flex;align-items:center;justify-content:center;flex:none}
.foot-item b{font-weight:700}
.copy{position:absolute;left:898px;top:26px;font-size:11px;line-height:15px}
</style>
</head>
<body>

<header class="topbar">
  <div class="brand">Corvane Lending Partners</div>
  <div class="contact-line" style="top:10px">
    <span class="dot"><svg width="12" height="12" viewBox="0 0 24 24"><path fill="#fff" d="M6.6 10.8a15 15 0 0 0 6.6 6.6l2.2-2.2c.3-.3.7-.4 1-.2 1.1.4 2.3.6 3.6.6.6 0 1 .4 1 1V20c0 .6-.4 1-1 1A17 17 0 0 1 3 4c0-.6.4-1 1-1h3.5c.6 0 1 .4 1 1 0 1.3.2 2.5.6 3.6.1.3 0 .7-.2 1z"/></svg></span>
    (555) 318-2740
  </div>
  <div class="contact-line" style="top:42px">
    <span class="dot"><svg width="12" height="12" viewBox="0 0 24 24"><path fill="#fff" d="M3 5h18v14H3zm2 2v.4l7 4.6 7-4.6V7z"/></svg></span>
    info@corvanelending.com
  </div>
</header>

<nav class="mainnav">
  <ul>
    <li class="active">HOME</li><li>ABOUT US</li><li>LOAN PROGRAMS</li><li>LOAN CLOSINGS</li><li>LOAN CRITERIA</li><li>NEWS</li><li>APPLY NOW</li><li>CONTACT US</li>
  </ul>
  <div class="social"><span></span><span></span><span></span></div>
</nav>

<section class="hero" role="img" aria-label="Glass office tower rising against a bright blue sky with clouds">
  <div class="hero-copy">
    <div class="kicker">WELCOME TO CORVANE LENDING PARTNERS</div>
    <h1>YOUR BUSINESS TO<br>KEEP UP</h1>
    <p>Lorem Ipsum is simply dummy text of the printing and typesetting industry. Lorem Ipsum hasbeen the industry's standard dummy text ever</p>
    <span class="btn">APPLY NOW</span>
  </div>
</section>

<section class="closed">
  <div class="eyebrow">RECENTLY</div>
  <h2 class="section-title">CLOSED LOANS</h2>
  <div class="rule"></div>
  <div class="arrow-btn" style="left:162px;top:254px"><svg width="10" height="10" viewBox="0 0 10 10"><path d="M7 1 3 5l4 4" fill="none" stroke="#888" stroke-width="1.5"/></svg></div>
  <div class="arrow-btn" style="left:997px;top:254px"><svg width="10" height="10" viewBox="0 0 10 10"><path d="M3 1l4 4-4 4" fill="none" stroke="#888" stroke-width="1.5"/></svg></div>
  <div class="loan-cards">
    <div class="loan-card"><div class="kind">OFFICE BUILDING</div><div class="amount">$ 2,750,000</div><div class="note">Discounted Payoff<br>Wall Township</div></div>
    <div class="loan-card featured"><div class="kind">MIXED USE</div><div class="amount">$ 1,125,000</div><div class="note">Refinance New York<br>New York</div></div>
    <div class="loan-card"><div class="kind">MIXED USE DEVELOPMENT</div><div class="amount">$ 12,550,000</div><div class="note">FefI/ Property Improvement<br>Paterson,NJ</div></div>
  </div>
</section>

<section class="about center">
  <div class="eyebrow">ABOUT US</div>
  <h2 class="section-title">CORVANE BUSINESS LENDING GROUP</h2>
  <div class="rule"></div>
  <p><b>Corvane Business Lending Services</b> Lorem Ipsum is simply dummy text of the printing and typesetting industry. Lorem Ipsum has been the industry's standard dummy text ever since the 1500s, when an unknown printer took a galley of type and scrambled it to make a type specimen book. It has survived not only five centuries, but also the leap into electronic typesetting, publishing software like Aldus PageMaker including versions of Lorem Ipsum</p>
  <span class="btn">READ MORE</span>
</section>

<section class="programs">
  <div class="eyebrow">SERVICES WE PROVIDE</div>
  <h2 class="section-title">LOAN PROGRAMS</h2>
  <div class="rule"></div>
  <p class="intro">Lorem Ipsum is simply dummy text of the printing and typesetting industry. Lorem Ipsum has been the industry's standard dummy text ever since the 1500s, when an unknown printer took a galley of type and scrambled it to make a type specimen book. It has survived not only five centuries, but also the leap into electronic typesetting, publishing software like Aldus PageMaker including versions of Lorem Ipsum</p>
  <div class="program-grid">
    <div class="program featured"><svg class="icon" viewBox="0 0 42 42"><circle cx="21" cy="21" r="19" fill="none" stroke="#fff" stroke-width="2"/><path d="M21 11a6 6 0 0 1 6 6c0 5-6 12-6 12s-6-7-6-12a6 6 0 0 1 6-6z" fill="#fff"/></svg><h3>LAND LOANS</h3><p>Lorem Ipsum is simply dummy text of the printing and typesetting industry</p></div>
    <div class="program"><svg class="icon" viewBox="0 0 42 42"><circle cx="21" cy="21" r="19" fill="none" stroke="#2f7de1" stroke-width="2"/><path d="M11 26h20M13 26a8 8 0 0 1 16 0M21 16v-2" fill="none" stroke="#2f7de1" stroke-width="2"/></svg><h3>HOSPITALITY LOANS</h3><p>Lorem Ipsum is simply dummy text of the printing and typesetting industry</p></div>
    <div class="program"><svg class="icon" viewBox="0 0 42 42"><circle cx="21" cy="21" r="19" fill="none" stroke="#2f7de1" stroke-width="2"/><path d="M12 30V18h6v12M18 30V12h6v18M24 30V20h6v10" fill="none" stroke="#2f7de1" stroke-width="2"/></svg><h3>MULTIFAMILY LOANS</h3><p>Lorem Ipsum is simply dummy text of the printing and typesetting industry</p></div>
    <div class="program"><svg class="icon" viewBox="0 0 42 42"><circle cx="21" cy="21" r="19" fill="none" stroke="#2f7de1" stroke-width="2"/><path d="M13 30V16h16v14M17 20h2M23 20h2M17 25h2M23 25h2" fill="none" stroke="#2f7de1" stroke-width="2"/></svg><h3>OFFICE LOANS</h3><p>Lorem Ipsum is simply dummy text of the printing and typesetting industry</p></div>
    <div class="program"><svg class="icon" viewBox="0 0 42 42"><circle cx="21" cy="21" r="19" fill="none" stroke="#2f7de1" stroke-width="2"/><circle cx="18" cy="18" r="5" fill="none" stroke="#2f7de1" stroke-width="2"/><path d="M12 30h18l-3-6h-12z" fill="none" stroke="#2f7de1" stroke-width="2"/></svg><h3>MIXED-USED- LOANS</h3><p>Lorem Ipsum is simply dummy text of the printing and typesetting industry</p></div>
    <div class="program"><svg class="icon" viewBox="0 0 42 42"><circle cx="21" cy="21" r="19" fill="none" stroke="#2f7de1" stroke-width="2"/><path d="M12 18h18l-2-5H14zM14 18v12h14V18M19 30v-6h4v6" fill="none" stroke="#2f7de1" stroke-width="2"/></svg><h3>RETAIL LOANS</h3><p>Lorem Ipsum is simply dummy text of the printing and typesetting industry</p></div>
    <div class="program"><svg class="icon" viewBox="0 0 42 42"><circle cx="21" cy="21" r="19" fill="none" stroke="#2f7de1" stroke-width="2"/><path d="M12 30V20l6-4v4l6-4v4l6-4v14z" fill="none" stroke="#2f7de1" stroke-width="2"/></svg><h3>INDUSTRIAL LOANS</h3><p>Lorem Ipsum is simply dummy text of the printing and typesetting industry</p></div>
    <div class="program"><svg class="icon" viewBox="0 0 42 42"><circle cx="21" cy="21" r="19" fill="none" stroke="#2f7de1" stroke-width="2"/><path d="M11 20l10-8 10 8M14 18v12h14V18M18 30v-6h6v6" fill="none" stroke="#2f7de1" stroke-width="2"/></svg><h3>WAREHOUSE LOANS</h3><p>Lorem Ipsum is simply dummy text of the printing and typesetting industry</p></div>
    <div class="program"><svg class="icon" viewBox="0 0 42 42"><circle cx="21" cy="21" r="19" fill="none" stroke="#2f7de1" stroke-width="2"/><path d="M12 30V17l9-5 9 5v13zM15 21h12M15 25h12" fill="none" stroke="#2f7de1" stroke-width="2"/></svg><h3>SELFSTORAGE LOANS</h3><p>Lorem Ipsum is simply dummy text of the printing and typesetting industry</p></div>
  </div>
</section>

<section class="team">
  <div class="eyebrow">PROFESINALS</div>
  <h2 class="section-title">OUR TEAM</h2>
  <div class="rule"></div>
  <div class="arrow-btn" style="left:104px;top:302px"><svg width="10" height="10" viewBox="0 0 10 10"><path d="M7 1 3 5l4 4" fill="none" stroke="#888" stroke-width="1.5"/></svg></div>
  <div class="arrow-btn" style="left:1056px;top:302px"><svg width="10" height="10" viewBox="0 0 10 10"><path d="M3 1l4 4-4 4" fill="none" stroke="#888" stroke-width="1.5"/></svg></div>

  <div class="member open" style="left:187px">
    <div class="photo" role="img" aria-label="Headshot of a smiling team member in shirt and tie" style="background:linear-gradient(160deg,#dfe8ef,#9fb3c4 60%,#6d8296)"></div>
    <div class="info">
      <span class="chev"><svg width="14" height="10" viewBox="0 0 14 10"><path d="M1 8l6-6 6 6" fill="none" stroke="#fff" stroke-width="2"/></svg></span>
      <div class="name">Mr. Owen Castell</div>
      <div class="role">Marketing Manager</div>
      <div class="detail"><svg width="14" height="14" viewBox="0 0 24 24"><path fill="#fff" d="M6.6 10.8a15 15 0 0 0 6.6 6.6l2.2-2.2c.3-.3.7-.4 1-.2 1.1.4 2.3.6 3.6.6.6 0 1 .4 1 1V20c0 .6-.4 1-1 1A17 17 0 0 1 3 4c0-.6.4-1 1-1h3.5c.6 0 1 .4 1 1 0 1.3.2 2.5.6 3.6.1.3 0 .7-.2 1z"/></svg><b>123 456 7890</b></div>
      <div class="detail small"><svg width="12" height="12" viewBox="0 0 24 24"><path fill="#fff" d="M3 5h18v14H3zm2 2v.4l7 4.6 7-4.6V7z"/></svg>info@owencastell.com</div>
    </div>
  </div>

  <div class="member" style="left:468px">
    <div class="photo" role="img" aria-label="Headshot of a team member in a light blazer in an office" style="background:linear-gradient(160deg,#e9ecef,#b9c3cc 55%,#7c8b98)"></div>
    <div class="info">
      <span class="chev"><svg width="14" height="10" viewBox="0 0 14 10"><path d="M1 2l6 6 6-6" fill="none" stroke="#fff" stroke-width="2"/></svg></span>
      <div class="name">Miss Lena Hartwell</div>
      <div class="role">C.E.O.</div>
    </div>
  </div>

  <div class="member" style="left:750px">
    <div class="photo" role="img" aria-label="Headshot of a team member in glasses and a light shirt" style="background:linear-gradient(160deg,#d7d8d6,#a7a59f 55%,#6e7376)"></div>
    <div class="info">
      <span class="chev"><svg width="14" height="10" viewBox="0 0 14 10"><path d="M1 2l6 6 6-6" fill="none" stroke="#fff" stroke-width="2"/></svg></span>
      <div class="name">Mr. Marcus Doyle</div>
      <div class="role">Marketing Officer</div>
    </div>
  </div>
</section>

<section class="news">
  <div class="eyebrow">LATEST</div>
  <h2 class="section-title">NEWS</h2>
  <div class="rule"></div>

  <article class="post" style="left:145px">
    <div class="frame"><div class="photo" role="img" aria-label="Modern glass office building under a blue sky" style="background:linear-gradient(180deg,#bfd8ee,#5e8fbf 60%,#7aa07a)"></div></div>
    <div class="date">31<br>oct</div>
    <h4>Lorem Ipsum is simply dummy text of the printing</h4>
    <div class="more">Read More <svg width="14" height="8" viewBox="0 0 14 8"><path d="M0 4h12M9 1l3 3-3 3" fill="none" stroke="#1d1d1d" stroke-width="1.5"/></svg></div>
  </article>

  <article class="post" style="left:483px">
    <div class="frame"><div class="photo" role="img" aria-label="Dark glass skyscraper seen from below" style="background:linear-gradient(160deg,#c9d0d6,#5a646d 55%,#2d3339)"></div></div>
    <div class="date">31<br>oct</div>
    <h4>Lorem Ipsum is simply dummy text of the printing</h4>
    <div class="more">Read More <svg width="14" height="8" viewBox="0 0 14 8"><path d="M0 4h12M9 1l3 3-3 3" fill="none" stroke="#1d1d1d" stroke-width="1.5"/></svg></div>
  </article>

  <article class="post" style="left:805px">
    <div class="frame"><div class="photo" role="img" aria-label="Warehouse aisle with shelving and a forklift" style="background:linear-gradient(160deg,#e6d9b8,#b48a4e 50%,#4f5f7a)"></div></div>
    <div class="date">31<br>oct</div>
    <h4>Lorem Ipsum is simply dummy text of the printing</h4>
    <div class="more">Read More <svg width="14" height="8" viewBox="0 0 14 8"><path d="M0 4h12M9 1l3 3-3 3" fill="none" stroke="#1d1d1d" stroke-width="1.5"/></svg></div>
  </article>
</section>

<footer class="footer">
  <div class="foot-item" style="left:143px">
    <span class="dot"><svg width="11" height="11" viewBox="0 0 24 24"><path fill="#2f7de1" d="M12 2a7 7 0 0 1 7 7c0 5-7 13-7 13S5 14 5 9a7 7 0 0 1 7-7zm0 4.5a2.5 2.5 0 1 0 0 5 2.5 2.5 0 0 0 0-5z"/></svg></span>
    <div><b>CORVANE LENDING PARTNERS</b><br>123, Loremum Dollar, Smit Amet - 123456</div>
  </div>
  <div class="foot-item" style="left:405px">
    <span class="dot"><svg width="11" height="11" viewBox="0 0 24 24"><path fill="#2f7de1" d="M6.6 10.8a15 15 0 0 0 6.6 6.6l2.2-2.2c.3-.3.7-.4 1-.2 1.1.4 2.3.6 3.6.6.6 0 1 .4 1 1V20c0 .6-.4 1-1 1A17 17 0 0 1 3 4c0-.6.4-1 1-1h3.5c.6 0 1 .4 1 1 0 1.3.2 2.5.6 3.6.1.3 0 .7-.2 1z"/></svg></span>
    <div><b>Call Us :</b><br>+123 456 7890</div>
  </div>
  <div class="foot-item" style="left:545px">
    <span class="dot"><svg width="11" height="11" viewBox="0 0 24 24"><path fill="#2f7de1" d="M3 5h18v14H3zm2 2v.4l7 4.6 7-4.6V7z"/></svg></span>
    <div><b>Email Us :</b><br>info@corvanelending.com</div>
  </div>
  <div class="copy">© 2016 Corvane Lending Partners.<br>All Rights Reserved.</div>
</footer>

</body>
</html>
```